Business Card for Coastal Tundrabridge Advisory

We need a business card for Coastal Tundrabridge Advisory. The company website address is provided below. The company logo is attached. We provide specialized permafrost services to the mining, transportation, and oil & gas industries. The card should be prepared for:
Matthias Korhonen, PhD.
Coastal Tundrabridge Advisory
PO Box 418259
Quillwater, Alaska 99642
Direct: +1-907-555-0143
Email: mkorhonen@tundrabridgeadvisory.example
Website: www.coastaltundrabridgeadvisory.example

```html
<!DOCTYPE html>
<html lang="en">
<head>
<meta charset="utf-8">
<title>Coastal Tundrabridge Advisory — Business Card</title>
<link href="https://fonts.googleapis.com/css2?family=Montserrat:wght@400;500;600;700&display=swap" rel="stylesheet">
<style>
  :root {
    --backdrop: #9b9b9b;
    --paper: #ffffff;
    --ink: #141a22;
    --navy: #0f1720;
    --navy-light: #1a2430;
    --white: #ffffff;
  }
  * { box-sizing: border-box; margin: 0; padding: 0; }
  html, body { width: 1093px; height: 1200px; overflow: hidden; }
  body {
    background: var(--backdrop);
    font-family: "Montserrat", Arial, sans-serif;
    color: var(--ink);
    position: relative;
  }
  .card {
    position: absolute;
    left: 265px;
    width: 580px;
    height: 360px;
    border-radius: 16px;
    overflow: hidden;
  }
  .card--front { top: 225px; background: var(--paper); }
  .card--back { top: 616px; background: var(--navy); }

  .brand-name {
    position: absolute;
    left: 300px;
    width: 200px;
    top: 414px;
    text-align: center;
    font-weight: 600;
    font-size: 15px;
    line-height: 19px;
    letter-spacing: 0.5px;
    color: var(--ink);
  }
  .divider {
    position: absolute;
    left: 241px;
    top: 122px;
    width: 1.5px;
    height: 166px;
    background: var(--ink);
  }
  .details {
    position: absolute;
    left: 250px;
    top: 120px;
  }
  .person-name { font-weight: 700; font-size: 19px; line-height: 22px; }
  .person-title { font-size: 13px; line-height: 18px; margin-top: 1px; }
  .address { font-size: 13.5px; line-height: 16.5px; margin-top: 10px; padding-left: 2px; }
  .contacts { list-style: none; margin-top: 14px; padding-left: 2px; }
  .contacts li {
    display: flex;
    align-items: center;
    gap: 11px;
    font-size: 13px;
    line-height: 16px;
    height: 25px;
  }
  .contacts svg { width: 13px; height: 13px; flex: none; }

  .pattern-field {
    position: absolute;
    inset: 0;
    background: linear-gradient(135deg, #3a3f46 0%, var(--navy-light) 38%, var(--navy) 70%);
    opacity: 0.8;
  }
  .brand-name--reversed {
    position: absolute;
    left: 190px;
    width: 200px;
    top: 280px;
    text-align: center;
    font-weight: 600;
    font-size: 15px;
    line-height: 19px;
    letter-spacing: 0.5px;
    color: var(--white);
  }
</style>
</head>
<body>
  <section class="card card--front" aria-label="Card front">
    <p class="brand-name" style="left:35px; top:189px;">Coastal Tundrabridge<br>Advisory</p>
    <div class="divider"></div>
    <div class="details">
      <h1 class="person-name">Matthias Korhonen, PhD.</h1>
      <p class="person-title">Managing Director</p>
      <p class="address">PO Box 418259<br>Quillwater, Alaska 99642</p>
      <ul class="contacts">
        <li>
          <svg viewBox="0 0 24 24" aria-hidden="true"><path fill="var(--ink)" d="M6.6 10.8a15.1 15.1 0 0 0 6.6 6.6l2.2-2.2a1 1 0 0 1 1-.25 11.4 11.4 0 0 0 3.6.57 1 1 0 0 1 1 1V20a1 1 0 0 1-1 1A17 17 0 0 1 3 4a1 1 0 0 1 1-1h3.5a1 1 0 0 1 1 1c0 1.25.2 2.45.57 3.57a1 1 0 0 1-.25 1z"/></svg>
          <span>+1-907-555-0143</span>
        </li>
        <li>
          <svg viewBox="0 0 24 24" aria-hidden="true"><path fill="var(--ink)" d="M2 5h20v14H2z"/><path fill="none" stroke="var(--paper)" stroke-width="1.8" d="M2 6l10 7 10-7"/></svg>
          <span>mkorhonen@tundrabridgeadvisory.example</span>
        </li>
        <li>
          <svg viewBox="0 0 24 24" aria-hidden="true"><circle cx="12" cy="12" r="10" fill="var(--ink)"/><path fill="none" stroke="var(--paper)" stroke-width="1.4" d="M2 12h20M12 2c3 3 3 17 0 20M12 2c-3 3-3 17 0 20"/></svg>
          <span>www.coastaltundrabridgeadvisory.example</span>
        </li>
      </ul>
    </div>
  </section>

  <section class="card card--back" aria-label="Card back">
    <div class="pattern-field" role="img" aria-label="Repeated faint company name pattern fading across the dark background"></div>
    <p class="brand-name--reversed">Coastal Tundrabridge<br>Advisory</p>
  </section>
</body>
</html>
```